Music Studio and Store Business Card and Logo Design

We need a business card and logo design for an existing Music Studio (Piano and Voice) which will soon expand to offer retail sheet music for all instruments including voice. The expanding store will not sell or lease instruments. We are a well known Fine Arts Studio for instruction to children, college students, and adults with 42 enrolled students and a wait list. We want something with simple elegance, but not archaic. Even a sleek modern look is okay. We do not want something childish or too fun looking because we do serve ages 5 - 62. We would also like the logo workable/transferable to signage for our new location opening in March. We like classic burgundy, black, deep blues, but are open to other suggestions. We included our studio brochure so you can get to know us a little better and some images we thought were interesting with the use of clef signs for the & and using note heads for the bottom or top of the letter "H"

Target Market(s)

All ages

Industry/Entity Type

Business

Contact Information for Business Card

H&H Music StudioPlattsburgh, NYWanda J. Haby and Oren M. Castaldi, Owners

Requirements
Must have
• Phone Number: (555) 817-4062
• Website: www.rbtonalartsroom.example
Nice to have
• Email: lorna@rbtonalartsroom.example
Should not have
• Any instruments on the card other than piano. Instrument pix is not a necessity.

```html
<!DOCTYPE html>
<html lang="en">
<head>
<meta charset="utf-8">
<title>R&amp;B Music Studio — Business Card</title>
<link rel="stylesheet" href="https://fonts.googleapis.com/css2?family=Open+Sans:wght@400;600;700&display=swap">
<style>
  :root {
    --backdrop: #8e8e8e;
    --card-black: #020202;
    --card-band: #161616;
    --ink-white: #ffffff;
    --ink-soft: #e6e6e6;
    --ink-muted: #cfcfcf;
  }
  * { box-sizing: border-box; margin: 0; padding: 0; }
  html, body {
    width: 1200px; height: 900px; overflow: hidden;
    background: var(--backdrop);
    font-family: "Open Sans", Arial, sans-serif;
  }
  .canvas {
    width: 1200px; height: 900px;
    display: flex; flex-direction: column;
    align-items: center; justify-content: center; gap: 48px;
  }
  .card {
    position: relative;
    width: 640px; height: 366px;
    background: var(--card-black);
    color: var(--ink-white);
    overflow: hidden;
    box-shadow: 0 6px 18px rgba(0,0,0,.25);
  }
  .stripe {
    position: absolute; left: 0; right: 0;
    height: 7px; background: var(--ink-white);
  }
  .stripe::after {
    content: ""; position: absolute; left: 0; right: 0;
    top: 11px; height: 2px; background: var(--ink-soft);
  }
  .studio-mark {
    position: absolute; left: 0; right: 0;
    display: flex; align-items: center; justify-content: center; gap: 14px;
    line-height: 1;
  }
  .studio-mark__dot {
    width: 18px; height: 18px; border-radius: 50%;
    background: var(--ink-white);
  }
  .studio-mark__name {
    font-weight: 600; font-size: 34px; letter-spacing: .03em;
    color: var(--ink-white);
  }

  /* back side */
  .card--back .studio-mark { top: 118px; }
  .card--back .stripe--main { top: 204px; }
  .card__contacts {
    position: absolute; top: 244px; left: 0; right: 0;
    text-align: center; font-size: 15px; line-height: 1.55;
    color: var(--ink-white);
  }
  .card__contact--email { color: var(--ink-muted); }
  .card--back .stripe--foot { top: 336px; }

  /* front side */
  .card__owners {
    position: absolute; top: 40px; left: 0; right: 0;
    text-align: center; line-height: 1.2;
  }
  .card__owner-name {
    font-weight: 700; font-size: 22px; text-transform: uppercase;
  }
  .card__owner-role {
    font-weight: 400; font-size: 14px; margin-top: 2px;
  }
  .card--front .studio-mark { top: 132px; }
  .card--front .studio-mark__name { font-size: 28px; }
  .card__band {
    position: absolute; left: 0; right: 0; top: 182px; height: 120px;
    background: var(--card-band);
  }
  .card--front .stripe--main { top: 200px; }
  .card__location {
    position: absolute; top: 238px; left: 0; right: 0;
    text-align: center; font-size: 17px; font-weight: 400;
  }
  .card--front .stripe--foot { top: 318px; }
</style>
</head>
<body>
  <main class="canvas">
    <section class="card card--back" aria-label="Card back">
      <div class="studio-mark">
        <span class="studio-mark__dot"></span>
        <span class="studio-mark__name">R&amp;B Music Studio</span>
      </div>
      <div class="stripe stripe--main"></div>
      <div class="card__contacts">
        <p class="card__contact">(555) 817-4062 &nbsp;·&nbsp; www.rbtonalartsroom.example</p>
        <p class="card__contact card__contact--email">lorna@rbtonalartsroom.example</p>
      </div>
      <div class="stripe stripe--foot"></div>
    </section>

    <section class="card card--front" aria-label="Card front">
      <div class="card__owners">
        <p class="card__owner-name">Lorna P. Quist</p>
        <p class="card__owner-name">Oren M. Castaldi</p>
        <p class="card__owner-role">Owners</p>
      </div>
      <div class="studio-mark">
        <span class="studio-mark__dot"></span>
        <span class="studio-mark__name">R&amp;B Music Studio</span>
      </div>
      <div class="card__band"></div>
      <div class="stripe stripe--main"></div>
      <p class="card__location">Maple Hollow, NY</p>
      <div class="stripe stripe--foot"></div>
    </section>
  </main>
</body>
</html>
```